Pinegate Marketing 8 page broshure

I need a design for an 8 page 8.5 X 11 booklet for my company. Our company colors are dark blue, light blue, and white. I am uploading some files for language that you may use. One of the files is our logo. please use the phrase: To us business is a contact sport as well as Pinegate Marketing is your complete marketing solution. Include something about we offer web and brochure design.as well as social media marketing.

Dear Velkan at Artisan Bazaar, Dear Velkan, we just spoke on the phone about my project for Pinegate Marketing Group sales brochure. As we discussed there are several things wrong with the final version that the Tumble sent to me. First of all the design is completely wrong, It is designed to be 8.5 x 11 when it should be designed to be 8.5 X 5.5 and the fold in the booklet should be the 8.5 side. In other words if you take and 8.5 x 11 piece of paper and fold in half that makes a booklet of 8.5 x 5.5. The other problem that were having with this is that there is no page covering our CRM product which is very important to our service offerings. I have sent you files that cover the CRM but for some reason it wasn't put in. Two small changes, on the front cover I see that we have on the very bottom of the of the page there is a line that says as well as Pinegate marketing is your complete marketing solution. I would like that line taken out. On the back cover I would like to change the address at the very bottom of the page the new address will be 41957 Kimber Ave., Westlake, OH 44163 I think if those changes are made we are about ready to go. Don't misunderstand we love your work, you guys have worked hard and the design is very good there just so's changes to make. Thank you very much, Oliver Marsh

Target Market(s)

Any business that needs help with increasing their sales and marketing in their company. We also have a fully customizable CRM so they may track the leads that are in their pipeline as well as those leads we bring in to their pipeline. On the marketing side we offer many services. Two things that I could not download was we do website design srvices and social media marketing.

Industry/Entity Type

It Company

Font styles to use
Sans Serif

Colors
0555a3
00a990
ffffff

Requirements
Must have
• Company logo on front cover, Stress the various services we offer on the marketing side, stress the CRM - very important. Feel free to use any of the dowloads I am sending to you for text.
Nice to have
• Very professional and elegant presentation.
Should not have
• Should not have any drawings or things that look out of place. Stock picture are fine as long as they have something to do with marketing or CRM.

```html
<!DOCTYPE html>
<html lang="en">
<head>
<meta charset="utf-8">
<title>Pinegate Marketing Group – Pages 2 &amp; 3</title>
<link href="https://fonts.googleapis.com/css2?family=Arimo:wght@400;500&display=swap" rel="stylesheet">
<style>
  :root {
    --backdrop: #e6e7e9;
    --paper: #ffffff;
    --heading-blue: #1b8bd0;
    --body-ink: #1d1d1d;
    --city-light: #cfe3f2;
    --city-mid: #6fa6cf;
    --city-deep: #1f4f7f;
    --globe-light: #f1f1f6;
    --globe-mid: #cfd0e2;
  }
  * { box-sizing: border-box; margin: 0; padding: 0; }
  html, body {
    width: 1200px; height: 800px; overflow: hidden;
    background: var(--backdrop);
    font-family: "Arimo", Arial, sans-serif;
  }
  .spread {
    position: absolute; left: 82px; top: 20px;
    width: 1036px; height: 760px;
    display: flex;
    box-shadow: 0 6px 24px rgba(0,0,0,.12);
  }
  .page {
    position: relative; width: 518px; height: 760px;
    background: var(--paper); overflow: hidden;
  }
  .page-content {
    position: relative; z-index: 2;
    padding: 44px 20px 0 20px;
  }
  .section-title {
    color: var(--heading-blue);
    font-weight: 400; font-size: 22px;
    text-align: center; letter-spacing: .2px;
    margin-bottom: 12px;
  }
  .mission-title { margin-top: 30px; margin-bottom: 14px; }
  .body-text {
    color: var(--body-ink);
    font-size: 10.4px; line-height: 14px;
    text-align: justify;
    margin-bottom: 14px;
  }
  .indent { text-indent: 16px; }
  .skyline {
    position: absolute; left: 0; right: 0; bottom: 0; height: 175px; z-index: 1;
    background: linear-gradient(to bottom, rgba(255,255,255,0) 0%, var(--city-light) 25%, var(--city-mid) 60%, var(--city-deep) 100%);
  }
  .globe {
    position: absolute; z-index: 1;
    right: -70px; top: 250px; width: 280px; height: 420px;
    border-radius: 50%;
    background: radial-gradient(circle at 40% 45%, var(--globe-light) 0%, var(--globe-mid) 70%, rgba(207,208,226,0) 100%);
    opacity: .75;
  }
</style>
</head>
<body>
  <main class="spread">
    <section class="page page-left">
      <div class="page-content">
        <h2 class="section-title">WHO IS PINEGATE MARKETING GROUP?</h2>
        <p class="body-text">In today’s technology paced environment, outsourcing has become an economic necessity for sales intensive companies. Pinegate Marketing Group acts as an agent representing High Tech Solutions Providers, Industrial Manufacturers, and Industrial Service Providers, and we feel confident that Pinegate Marketing Group is the premier outsourced lead generation company in the United States. Our “hands on” approach of becoming intrinsically familiar with each client’s product or service enables us to create a marketing strategy unique to each client. This concept has led to successful lead generation projects for companies such as Norvane Systems, Petalworks, Quorum Data, Harlow Steel, Kestrel Dynamics, Brookfield Chemical, Meridian Insurance, and Northline Graphics. At Pinegate Marketing Group we are experts at helping our clients “go to market” with their product, thus rapidly growing their sales. We can determine which prospects are “in the market” to purchase a client’s product or service at any given time, eliminating the frustration of cold calling.</p>
        <p class="body-text indent">The corporate philosophy of Pinegate Marketing Group sets an industry standard; “We will, at all times, put our client’s interest before our own, doing what is right as opposed to increasing corporate profits at the expense of our clients”.</p>
        <p class="body-text">Pinegate Marketing Group intends to remain the United States’ premier provider of outsourced lead generation. Our representatives have performed outsource marketing assignments for many businesses throughout the United States and we are proud to say that our first client is still our client. We strive to maintain partnerships with our clients and every effort is made to insure client satisfaction.</p>
        <h2 class="section-title mission-title">OUR MISSION STATEMENT</h2>
        <p class="body-text">The mission statement of Pinegate Marketing Group has not changed since its inception in 1994. We continue to strive to be the best marketing and lead generation firm in the United States. Our highly talented, highly trained, experienced and motivated staff anchors our efforts. We will do whatever it takes to insure our clients that they are receiving the highest return on their investment. We will never cut corners or think only “in the box” like others in our industry. We will represent our client’s interests as we would represent our own. Our long term goals are much more important than short term profits. Our promises will be kept at all costs and we will continue, through hard work and dedication to our clients, to be the number one marketing firm in the United States.</p>
      </div>
      <div class="skyline" role="img" aria-label="Photograph of a blue-toned city skyline"></div>
    </section>
    <section class="page page-right">
      <div class="globe" role="img" aria-label="Faint illustration of a globe"></div>
      <div class="page-content">
        <h2 class="section-title">SERVICES OFFERED</h2>
        <p class="body-text">Pinegate Marketing is proud to offer the following services:</p>
        <p class="body-text">We provide the best, most productive, cost effective (ROI) outbound Lead Generation service in the country.</p>
        <p class="body-text">Pinegate Marketing can offer not only Outbound Lead Generation but there is great success in Inbound Marketing. We will field your inbound calls relating to sales prospects as well as your customer questions and complaints.</p>
        <p class="body-text">Effective Email Campaigns. This type of marketing can easily be combined with the outbound and inbound strategies.</p>
        <p class="body-text">Direct Mail. From the database generated specifically for your company we can do a Direct Mail campaign.</p>
        <p class="body-text">We can provide expert training for Sales Representatives as well as expert training of Outbound and Inbound Representatives. We have been around for over 23 years in this business. We know what works and what doesn’t work. Many things go into the training of these employees. There is a big difference between a person who say’s they are a salesperson or a telemarketing person and a trained expert trained by us. There are statistics that show a Salesperson can be the best thing your company can do or the worst thing and most expensive employee within your company.</p>
      </div>
      <div class="skyline" role="img" aria-label="Photograph of a blue-toned city skyline"></div>
    </section>
  </main>
</body>
</html>
```